Business Card Design for Vintage Jazz

I am a vintage jazz band leader in New York City. My groups play the music of the 1920s, 1930s and 1940s. My website is morvalquist.com for more info on what I do.

I am looking for a two sided business card design that has the look and feel of a really nice business card from the 1930s. I need to convey with the design that my work has that vintage kind of class and style, but also conveys that we are fun and entertaining.

Most importantly it should make a bold staement. If Hal Denbrook had a card, what would it have looked like? I want a card that I feel confident will make an impact and will let people know that my work is te the top that NYC has to offer in vintage jazz..

Note that I have only decided to avoid the "committed payment" option as I have not used this service before. Assuming that I get quality work I will select a design from those presented.

Target Market(s)

people who want to hire my band for events, media, and new fans of the band

Industry/Entity Type

Performing Art

Contact Information for Business Card

Definitely a matte finish, possibly a sort of old style of paper with that brown tint? definitely a thick card.

Requirements
Must have
• FRONT
• My name: Tobin Vashley
• What I do: Bandleader, Guitarist, Vocalist, Songwriter
• Contact Details: morvalquist.com tobin@morvalquist.com 646-555-0148
• BACK
• My Social Media Links:
• facebook.morvalquist.com
• twitter, instagram, linkedin: morvalquist
• I'm also including a photo image I would like to use. The photo's background is not needed, and to be honest isn't really desireable. Just looking to use the image of me.
Nice to have
• I'm attaching which could be used as is, omitted from the card, or altered maybe with text going around the outside of the circle or in some other way. It may need some clean up to the edges of the lettering as we only use it for the website thumbnail.
• If there's space I'd like to include the text "join our mailing list for a free song download: freesong.morvalquist.com" If not perhaps just "Download a Free Song at: freesong.morvalquist.com - something to this end.
Should not have
• anything cartoony. Don't think retro 90s's vision of the swing era, think actual swing era!
• anything modern. Got to look old school
• Try to avoid dark backgrounds. Since we often play in bars and clubs where it is dar, a d
• avoid script fonts.

```html
<!DOCTYPE html>
<html lang="en">
<head>
<meta charset="utf-8">
<title>Tobin Vashley – Business Card</title>
<link rel="stylesheet" href="https://fonts.googleapis.com/css2?family=Open+Sans:wght@400;600;700&display=swap">
<style>
  :root {
    --ink: #000000;
    --paper: #ffffff;
    --stage: #e9e6e1;
    --photo-light: #d9d9d9;
    --photo-dark: #3a3a3a;
    --card-shadow: rgba(0, 0, 0, 0.18);
  }
  * { margin: 0; padding: 0; box-sizing: border-box; }
  html, body {
    width: 1200px; height: 900px; overflow: hidden;
    background: var(--stage);
    font-family: "Open Sans", Arial, sans-serif;
    color: var(--ink);
  }
  .card {
    position: absolute;
    left: 250px;
    width: 700px; height: 400px;
    background: var(--paper);
    overflow: hidden;
    box-shadow: 0 6px 18px var(--card-shadow);
  }
  .card--back { top: 30px; }
  .card--front { top: 470px; }

  /* Back side: social links */
  .back-band {
    position: absolute; left: 0; top: 0;
    width: 100%; height: 222px;
    background: var(--ink);
  }
  .back-name {
    position: absolute; left: 0; top: 106px; width: 100%;
    text-align: center;
    color: var(--paper);
    font-weight: 700; font-size: 44px; letter-spacing: 0.5px;
  }
  .social {
    position: absolute; top: 250px;
    font-size: 17px; line-height: 24px;
  }
  .social--left { right: 372px; text-align: right; }
  .social--right { left: 382px; }
  .social-row { display: flex; align-items: center; gap: 8px; }
  .social--left .social-row { justify-content: flex-end; }
  .social-mark {
    display: inline-block; width: 15px; height: 15px;
    background: var(--ink);
  }
  .roles {
    position: absolute; left: 0; top: 326px; width: 100%;
    text-align: center;
    font-weight: 700; font-size: 19px; letter-spacing: 1px;
  }

  /* Front side: portrait and contact */
  .front-band {
    position: absolute; left: 300px; top: 196px;
    width: 400px; height: 204px;
    background: var(--ink);
  }
  .portrait {
    position: absolute; left: 20px; top: 38px;
    width: 330px; height: 362px;
    background: linear-gradient(160deg, var(--photo-light) 0%, #9a9a9a 40%, var(--photo-dark) 100%);
  }
  .monogram {
    position: absolute; right: 40px; top: 70px;
    font-weight: 400; font-size: 26px; letter-spacing: 2px;
  }
  .monogram-ring {
    display: inline-block; width: 14px; height: 14px;
    border: 2px solid var(--ink); border-radius: 50%;
    margin-right: 8px; vertical-align: middle;
  }
  .front-name {
    position: absolute; right: 36px; top: 214px;
    color: var(--paper);
    font-weight: 700; font-size: 30px;
  }
  .contact {
    position: absolute; right: 36px; top: 268px;
    color: var(--paper);
    font-size: 16px; line-height: 26px;
    text-align: right;
  }
  .contact-row { display: flex; justify-content: flex-end; align-items: center; gap: 8px; }
  .contact-icon { width: 13px; height: 13px; fill: var(--paper); stroke: var(--paper); }
</style>
</head>
<body>

<section class="card card--back" aria-label="Card back">
  <div class="back-band"></div>
  <h1 class="back-name">Tobin Vashley</h1>

  <div class="social social--left">
    <div class="social-row">morvalquist.com <span class="social-mark"></span></div>
    <div class="social-row">morvalquist <span class="social-mark"></span></div>
  </div>
  <div class="social social--right">
    <div class="social-row"><span class="social-mark"></span> @morvalquist</div>
    <div class="social-row"><span class="social-mark"></span> @morvalquist</div>
  </div>

  <p class="roles">BANDLEADER, GUITARIST, VOCALIST, SONGWRITER</p>
</section>

<section class="card card--front" aria-label="Card front">
  <div class="front-band"></div>
  <div class="portrait" role="img" aria-label="Black and white cut-out portrait of the bandleader tipping a straw boater hat, wearing a piped blazer and cravat"></div>

  <div class="monogram"><span class="monogram-ring"></span>Tobin Vashley</div>

  <h2 class="front-name">Tobin Vashley</h2>
  <div class="contact">
    <div class="contact-row">646-555-0148
      <svg class="contact-icon" viewBox="0 0 16 16"><path stroke="none" d="M3 1l3 3-1.5 2a9 9 0 0 0 5.5 5.5L12 10l3 3-2 2C7 15 1 9 1 3z"/></svg>
    </div>
    <div class="contact-row">tobin@morvalquist.com
      <svg class="contact-icon" viewBox="0 0 16 16"><rect x="1" y="3" width="14" height="10" stroke="none"/><path d="M1 3l7 6 7-6" fill="none" stroke="#000" stroke-width="1.4"/></svg>
    </div>
    <div class="contact-row">morvalquist.com
      <svg class="contact-icon" viewBox="0 0 16 16"><circle cx="8" cy="8" r="7" stroke="none"/><path d="M1 8h14M8 1c-3 3-3 11 0 14M8 1c3 3 3 11 0 14" fill="none" stroke="#000" stroke-width="1.2"/></svg>
    </div>
  </div>
</section>

</body>
</html>
```